Kelo Wave Mint Business cards

Logo, tag line and photo on card
Agent Name
Title
Address
Phone number
Email
Website
Make logo on one side large by rotating  to portrait format.  Keep the background of the logo white.

Contact Information for Business Card
Slogan; Making Every Wave Count

```html
<!DOCTYPE html>
<html lang="en">
<head>
<meta charset="utf-8">
<title>Kelo Wave Mint – Business Cards</title>
<link rel="stylesheet" href="https://fonts.googleapis.com/css2?family=Montserrat:wght@700;800&family=Open+Sans:wght@400;600&display=swap">
<style>
  :root {
    --navy: #22306a;
    --navy-deep: #1b2658;
    --red: #c62828;
    --coral: #e5533a;
    --white: #ffffff;
    --ink: #1a1a1a;
    --stage: #262626;
    --photo-light: #8a8f9e;
    --photo-dark: #3a4160;
  }
  * { margin: 0; padding: 0; box-sizing: border-box; }
  html, body { width: 1200px; height: 780px; overflow: hidden; }
  body {
    background: var(--stage);
    position: relative;
    font-family: "Open Sans", sans-serif;
  }
  .card {
    position: absolute;
    width: 540px;
    height: 309px;
    border-radius: 16px;
    overflow: hidden;
    box-shadow: 0 14px 30px rgba(0,0,0,.45);
  }
  /* Back side */
  .card-back { left: 40px; top: 235px; background: var(--navy); }
  .back-logo {
    position: absolute;
    left: 50%; top: 50%;
    transform: translate(-50%, -50%);
    width: 160px; height: 200px;
    border: 5px solid var(--coral);
    border-radius: 14px;
    display: flex; flex-direction: column;
    justify-content: center; align-items: center;
    gap: 2px;
  }
  .back-logo .brand-word {
    font-family: "Montserrat", sans-serif;
    font-weight: 800;
    font-size: 40px;
    line-height: 1.05;
    color: var(--white);
  }
  /* Front side */
  .card-front { left: 620px; top: 235px; background: var(--white); }
  .front-shapes { position: absolute; inset: 0; }
  .front-logo {
    position: absolute; left: 20px; top: 20px;
    width: 100px; height: 100px;
    border: 4px solid var(--red);
    border-radius: 8px;
    display: flex; flex-direction: column;
    justify-content: center; padding-left: 10px;
  }
  .front-logo .brand-word {
    font-family: "Montserrat", sans-serif;
    font-weight: 800;
    font-size: 21px;
    line-height: 1.05;
    color: var(--navy);
  }
  .agent {
    position: absolute; right: 58px; top: 22px;
    text-align: right;
  }
  .agent-name {
    font-family: "Montserrat", sans-serif;
    font-weight: 800;
    font-size: 27px;
    line-height: 1;
  }
  .agent-name .first { color: var(--red); }
  .agent-name .last { color: var(--navy); }
  .agent-title {
    font-family: "Montserrat", sans-serif;
    font-weight: 700;
    font-size: 14px;
    color: var(--ink);
    margin-top: 3px;
  }
  .address {
    position: absolute; left: 24px; top: 136px;
    font-size: 12px; line-height: 1.35; color: var(--ink);
  }
  .contact-list {
    position: absolute; left: 24px; top: 178px;
    list-style: none;
    font-size: 12px; color: var(--ink);
  }
  .contact-list li {
    display: flex; align-items: center; gap: 7px;
    height: 18px;
  }
  .contact-list svg { width: 12px; height: 12px; flex: none; }
  .photo {
    position: absolute; left: 375px; top: 90px;
    width: 128px; height: 128px; border-radius: 50%;
    border: 3px solid var(--red);
    box-shadow: 0 0 0 5px var(--white);
    background: radial-gradient(circle at 55% 40%, var(--photo-light) 0%, var(--photo-dark) 55%, var(--navy) 100%);
  }
  .slogan {
    position: absolute; right: 22px; bottom: 18px;
    font-size: 12px; color: var(--white); letter-spacing: .2px;
  }
</style>
</head>
<body>

<section class="card card-back" aria-label="Card back">
  <div class="back-logo">
    <span class="brand-word">Kelo</span>
    <span class="brand-word">Wave</span>
    <span class="brand-word">Mint</span>
  </div>
</section>

<section class="card card-front" aria-label="Card front">
  <svg class="front-shapes" viewBox="0 0 540 309" preserveAspectRatio="none" aria-hidden="true">
    <rect x="505" y="0" width="35" height="48" fill="var(--navy)"/>
    <path d="M540 128 L480 128 C430 210 310 292 70 309 L540 309 Z" fill="var(--navy)"/>
    <path d="M58 276 C210 292 320 268 392 224 C330 278 220 300 70 296 Z" fill="var(--red)"/>
  </svg>

  <div class="front-logo">
    <span class="brand-word">Kelo</span>
    <span class="brand-word">Wave</span>
    <span class="brand-word">Mint</span>
  </div>

  <div class="agent">
    <div class="agent-name"><span class="first">Dalen</span> <span class="last">Verhoek</span></div>
    <div class="agent-title">Co-Founder</div>
  </div>

  <p class="address">1840 Harlow Ave. Suite 310<br>Linden Falls, TX 75990</p>

  <ul class="contact-list">
    <li>
      <svg viewBox="0 0 24 24"><path fill="var(--red)" d="M6.6 10.8a15 15 0 0 0 6.6 6.6l2.2-2.2a1 1 0 0 1 1-.25 11.4 11.4 0 0 0 3.6.57 1 1 0 0 1 1 1V20a1 1 0 0 1-1 1A17 17 0 0 1 3 4a1 1 0 0 1 1-1h3.5a1 1 0 0 1 1 1c0 1.25.2 2.45.57 3.6a1 1 0 0 1-.25 1z"/></svg>
      (555) 014-2290
    </li>
    <li>
      <svg viewBox="0 0 24 24"><rect x="2" y="5" width="20" height="14" rx="2" fill="var(--red)"/><path d="M3 6l9 7 9-7" stroke="#fff" stroke-width="1.8" fill="none"/></svg>
      info@website.com
    </li>
    <li>
      <svg viewBox="0 0 24 24"><circle cx="12" cy="12" r="10" fill="var(--red)"/><path d="M2 12h20M12 2c3 3 3 17 0 20M12 2c-3 3-3 17 0 20" stroke="#fff" stroke-width="1.4" fill="none"/></svg>
      www.website.com
    </li>
  </ul>

  <div class="photo" role="img" aria-label="Portrait photo of the co-founder"></div>

  <p class="slogan">Making Every Wave Count</p>
</section>

</body>
</html>
```